Boutique custom software development company needs new business card

Our nearly 20 year old custom software development company would like to better include the fact that we are now providing Bitcoin services. These new services are B2B include education (how to acquire and securely hold Bitcoin) and integrating Bitcoin payments into existing ecommerce sites or other existing systems. Please keep the card clean and simple. Attached is our current design and some other files. vextorial.com

Target Market(s)

businesses owners interested in long term relationship

Industry/Entity Type

Custom software development and Bitcoin

Contact Information for Business Card

Dale Parker, dale@vextorial.com, vextorial.com, (888) 555-VXTRL

Font styles to use
Other font styles liked:
• monospace

Requirements
Must have
• double-sided
Nice to have
• clean and simple
Should not have
• physical address

```html
<!DOCTYPE html>
<html lang="en">
<head>
<meta charset="utf-8">
<title>Vextorial business card</title>
<link rel="stylesheet" href="https://fonts.googleapis.com/css2?family=Montserrat:wght@400;500;800&display=swap">
<style>
  :root {
    --page: #b9b9b9;
    --card: #ffffff;
    --blue: #3f73b9;
    --orange: #f07d22;
    --white: #ffffff;
  }
  * { box-sizing: border-box; margin: 0; padding: 0; }
  html, body {
    width: 1200px; height: 800px; overflow: hidden;
    background: var(--page);
    font-family: "Montserrat", sans-serif;
  }
  .stage {
    position: relative; width: 1200px; height: 800px;
    display: flex; align-items: center; justify-content: center; gap: 60px;
  }
  .card {
    position: relative; width: 525px; height: 300px;
    background: var(--card); border-radius: 22px; overflow: hidden;
    box-shadow: 0 14px 30px rgba(0,0,0,0.25);
  }
  /* front side */
  .name {
    position: absolute; left: 38px; top: 92px;
    font-weight: 800; font-size: 27px; letter-spacing: 0.5px; text-transform: uppercase;
  }
  .name .first { color: var(--orange); }
  .name .last { color: var(--blue); }
  .contact-band {
    position: absolute; left: 0; top: 168px; width: 330px; height: 90px;
    background: var(--blue);
    padding: 10px 0 0 38px;
    list-style: none;
  }
  .contact-band li {
    display: flex; align-items: center; gap: 10px;
    height: 24px; color: var(--white); font-size: 14.5px; font-weight: 500;
  }
  .icon {
    width: 20px; height: 20px; border-radius: 3px; background: var(--white);
    display: flex; align-items: center; justify-content: center; flex: none;
  }
  .mark-square {
    position: absolute; left: 346px; top: 96px; width: 104px; height: 104px;
    background: var(--blue);
  }
  .accent-square {
    position: absolute; left: 462px; top: 30px; width: 63px; height: 80px;
    background: var(--orange);
  }
  /* back side */
  .back { display: flex; flex-direction: column; align-items: center; justify-content: center; }
  .brand {
    color: var(--blue); font-weight: 800; font-size: 66px; line-height: 1;
    letter-spacing: -1px; text-transform: uppercase;
  }
  .tagline {
    margin-top: 8px; color: var(--blue); font-weight: 400; font-size: 22px;
  }
</style>
</head>
<body>
<main class="stage">
  <section class="card front" aria-label="Card front">
    <h1 class="name"><span class="first">Dale</span> <span class="last">Parker</span></h1>
    <ul class="contact-band">
      <li>
        <span class="icon">
          <svg width="14" height="14" viewBox="0 0 24 24"><path fill="#f07d22" d="M6.6 10.8a15 15 0 0 0 6.6 6.6l2.2-2.2c.3-.3.7-.4 1-.2 1.1.4 2.3.6 3.6.6.6 0 1 .4 1 1V20c0 .6-.4 1-1 1A17 17 0 0 1 3 4c0-.6.4-1 1-1h3.5c.6 0 1 .4 1 1 0 1.3.2 2.5.6 3.6.1.3 0 .7-.2 1z"/></svg>
        </span>
        (888) 555-VXTRL
      </li>
      <li>
        <span class="icon">
          <svg width="14" height="14" viewBox="0 0 24 24"><rect x="2" y="5" width="20" height="14" rx="1" fill="#f07d22"/><path d="M2 6l10 7 10-7" fill="none" stroke="#fff" stroke-width="2"/></svg>
        </span>
        dale@vextorial.com
      </li>
      <li>
        <span class="icon">
          <svg width="14" height="14" viewBox="0 0 24 24"><circle cx="12" cy="12" r="10" fill="#f07d22"/><path d="M2 12h20M12 2c3 3 3 17 0 20M12 2c-3 3-3 17 0 20" fill="none" stroke="#fff" stroke-width="1.5"/></svg>
        </span>
        www.vextorial.com
      </li>
    </ul>
    <div class="mark-square"></div>
    <div class="accent-square"></div>
  </section>

  <section class="card back" aria-label="Card back">
    <p class="brand">Vextorial</p>
    <p class="tagline">developer of custom applications</p>
  </section>
</main>
</body>
</html>
```